Brightway Carpet and Tile cleaning Business card Design

I need a design that has the same feel as my van.
i would also like a prominent "Review us on facebook" somewhere, but not that it makes it look silly.
I would like the card to have a little bit of grey or black in the design as well.

It will need contact details
phone: 0455 817264
email: rkbrightwayclean@mailbox-example.com
website: www.brightwaycarpetandtilecleaning-example.com.au
facebook: /brightwaycarpetandtilecleaning

Industry/Entity Type

Business

Contact Information for Business Card

Phone number 0455817264
Email rkbrightwayclean@mailbox-example.com
Website www.brightwaycarpetandtilecleaning-example.com.au
Facebook/brightwaycarpetandtilecleaning

Colors
000000

Requirements
Must have
• Same feel as my van
• I want the card to stand out from the crowd
Nice to have
• Maybe include a tiny bit of a third colour? Grey's,blacks, orange?

```html
<!DOCTYPE html>
<html lang="en">
<head>
<meta charset="utf-8">
<title>Brightway Carpet and Tile Cleaning – Business Card</title>
<link rel="stylesheet" href="https://fonts.googleapis.com/css2?family=Exo+2:wght@700&family=Open+Sans:wght@400;600&display=swap">
<style>
  :root {
    --page: #3a3a3a;
    --white: #ffffff;
    --blue: #1ab4e2;
    --green: #8cc63f;
    --ink-dark: #1b1c1e;
    --ink-soft: #2a2c2f;
    --grey-text: #e6e6e6;
    --brand-blue: #22a9dc;
  }
  * { margin: 0; padding: 0; box-sizing: border-box; }
  html, body { width: 1105px; height: 1200px; overflow: hidden; }
  body {
    background: var(--page);
    position: relative;
    font-family: "Open Sans", Arial, sans-serif;
  }
  .card {
    position: absolute;
    left: 192px;
    width: 720px;
    height: 411px;
    overflow: hidden;
    box-shadow: 0 4px 14px rgba(0,0,0,.45);
  }
  .card--front { top: 146px; background: var(--white); }
  .card--back {
    top: 602px;
    background: linear-gradient(110deg, var(--ink-dark) 0%, var(--ink-soft) 55%, #4a4c50 70%, var(--ink-dark) 85%);
  }
  .card__waves { position: absolute; left: 0; top: 0; width: 720px; height: 411px; }

  .brand {
    position: absolute;
    font-family: "Exo 2", Arial, sans-serif;
    font-weight: 700;
    color: var(--brand-blue);
    display: flex;
    align-items: center;
    gap: 14px;
    white-space: nowrap;
  }
  .brand__dot {
    width: 22px; height: 22px; border-radius: 50%;
    background: var(--green);
    flex: none;
  }
  .brand__name { font-size: 50px; line-height: 1; }
  .brand__tagline { font-size: 21px; letter-spacing: 2px; line-height: 1; margin-top: 8px; }
  .card--front .brand { left: 250px; top: 112px; }
  .card--back .brand { left: 130px; top: 165px; }

  .contact-list {
    position: absolute;
    left: 30px;
    top: 276px;
    list-style: none;
    color: var(--white);
    font-size: 16px;
  }
  .contact-list li {
    display: flex;
    align-items: center;
    gap: 12px;
    height: 28px;
  }
  .contact-list svg { width: 18px; height: 18px; flex: none; }
  .icon-square { width: 15px; height: 15px; background: var(--white); flex: none; margin: 0 1px; }

  .holder {
    position: absolute;
    right: 40px;
    top: 330px;
    text-align: center;
    color: var(--white);
    font-family: "Exo 2", Arial, sans-serif;
    font-weight: 700;
  }
  .holder__name { font-size: 24px; letter-spacing: 1px; }
  .holder__role { font-size: 19px; margin-top: 2px; opacity: .95; }

  .back__website {
    position: absolute;
    left: 0; right: 0;
    top: 292px;
    text-align: center;
    color: var(--grey-text);
    font-size: 19px;
    letter-spacing: .5px;
  }
  .review {
    position: absolute;
    left: 0; right: 0;
    top: 336px;
    display: flex;
    justify-content: center;
    align-items: center;
    gap: 16px;
    font-family: "Exo 2", Arial, sans-serif;
    font-weight: 700;
    font-size: 29px;
    color: var(--brand-blue);
  }
  .review__square { width: 26px; height: 26px; background: var(--green); }
</style>
</head>
<body>

  <section class="card card--front" aria-label="Business card front">
    <svg class="card__waves" viewBox="0 0 720 411" aria-hidden="true">
      <path d="M0 206 C120 170 220 175 330 220 C430 262 520 270 720 220 L720 411 L0 411 Z" fill="var(--green)"/>
      <path d="M0 232 C120 200 230 208 340 245 C440 280 540 290 720 245 L720 411 L0 411 Z" fill="var(--blue)"/>
    </svg>

    <div class="brand">
      <span class="brand__dot"></span>
      <div>
        <div class="brand__name">Brightway Clean</div>
        <div class="brand__tagline">CARPET &amp; TILE CLEANING</div>
      </div>
    </div>

    <ul class="contact-list">
      <li>
        <svg viewBox="0 0 24 24" aria-hidden="true"><path fill="#fff" d="M6.6 10.8a15.1 15.1 0 0 0 6.6 6.6l2.2-2.2c.3-.3.7-.4 1-.2 1.1.4 2.3.6 3.6.6.6 0 1 .4 1 1V20c0 .6-.4 1-1 1C10.6 21 3 13.4 3 4c0-.6.4-1 1-1h3.5c.6 0 1 .4 1 1 0 1.3.2 2.5.6 3.6.1.3 0 .7-.2 1z"/></svg>
        <span>0455817264</span>
      </li>
      <li>
        <svg viewBox="0 0 24 24" aria-hidden="true"><rect x="2" y="5" width="20" height="14" rx="1" fill="#fff"/><path d="M3 6l9 7 9-7" fill="none" stroke="var(--blue)" stroke-width="1.6"/></svg>
        <span>rkbrightwayclean@mailbox-example.com</span>
      </li>
      <li>
        <svg viewBox="0 0 24 24" aria-hidden="true"><circle cx="12" cy="12" r="9" fill="#fff"/><path d="M3 12h18M12 3c3 3 3 15 0 18M12 3c-3 3-3 15 0 18" fill="none" stroke="var(--blue)" stroke-width="1.4"/></svg>
        <span>www.brightwaycarpetandtilecleaning-example.com.au</span>
      </li>
      <li>
        <span class="icon-square"></span>
        <span>/brightwaycarpetandtilecleaning</span>
      </li>
    </ul>

    <div class="holder">
      <div class="holder__name">RYAN KESSLER</div>
      <div class="holder__role">OWNER/OPERATOR</div>
    </div>
  </section>

  <section class="card card--back" aria-label="Business card back">
    <div class="brand">
      <span class="brand__dot"></span>
      <div>
        <div class="brand__name">Brightway Clean</div>
        <div class="brand__tagline">CARPET &amp; TILE CLEANING</div>
      </div>
    </div>

    <div class="back__website">WWW.BRIGHTWAYCARPETANDTILECLEANING-EXAMPLE.COM.AU</div>

    <div class="review">
      <span>REVIEW US ON</span>
      <span class="review__square"></span>
    </div>
  </section>

</body>
</html>
```